Allied Health team of Physiotherapists & Occupational Therapists seek a business card design

We have our new logo, we now need our new business cards and stationary. Tidewell: Oedema & Family Clinic is seeking a generic card design to represent our whole team and individual cards for each therapist that incorporates our new logo to communicate our holistic approach that is calming, nuturing, supportive and welcoming.
Our Physiotherapists and Occupational Therapists assess, treat and provide education for people who are at risk of or who have lymphoedema. This is often as a result of treatment for cancer. We provide pre-operative and post-operative management and cancer rehabilitation in our Pilates studio. Our team also consists of Physiotherapists who have a strong interest in pelvic floor and continence management for both men and women.

Target Market(s)

Mainly women health conscious

Industry/Entity Type

Allied Health: Physiotherapy / Occupational Therapy

Contact Information for Business Card

Address: 14 Gallivant Ave Frankston 3199 Phone: 84316570 fax: 8431 6578 Email: info@tidewellcareservices.com.au Website: tidewellcareservices.com.au Facebook address: facebook.com/TidewellOedemaAndFamilyCareClinic. Room to write appointments. Individual cards need to have name, office email and individual email and professional details

Requirements
Must have
• Logo as per uploaded documents

```html
<!DOCTYPE html>
<html lang="en">
<head>
<meta charset="utf-8">
<title>Tidewell: Oedema &amp; Family Clinic — Business Card</title>
<link rel="stylesheet" href="https://fonts.googleapis.com/css2?family=Cinzel:wght@700&family=Open+Sans:wght@400;600&display=swap">
<style>
  :root {
    --peach: #f8af83;
    --peach-light: #fccfad;
    --sage: #c5cec5;
    --white: #ffffff;
    --ink: #2a2a2a;
    --stage: #eeeae6;
    --text-font: "Open Sans", Arial, sans-serif;
    --name-font: "Cinzel", Georgia, serif;
  }
  * { box-sizing: border-box; margin: 0; padding: 0; }
  html, body { width: 1200px; height: 920px; overflow: hidden; }
  body {
    background: var(--stage);
    font-family: var(--text-font);
    display: flex;
    flex-direction: column;
    align-items: center;
    justify-content: center;
    gap: 54px;
  }
  .card {
    position: relative;
    width: 600px;
    height: 343px;
    overflow: hidden;
    box-shadow: 0 6px 18px rgba(0,0,0,0.12);
  }
  .card-back { background: var(--peach); }
  .card-front { background: var(--white); }
  .card-waves { position: absolute; inset: 0; width: 100%; height: 100%; }

  .brand {
    position: absolute;
    display: flex;
    align-items: center;
    gap: 10px;
    font-family: var(--text-font);
    font-weight: 600;
    font-size: 17px;
    line-height: 1.3;
    text-align: left;
  }
  .brand-dot { width: 14px; height: 14px; border-radius: 50%; flex: none; }
  .card-back .brand { left: 200px; top: 56px; color: var(--white); }
  .card-back .brand-dot { background: var(--white); }
  .card-front .brand { left: 44px; top: 92px; color: var(--peach); }
  .card-front .brand-dot { background: var(--peach); }

  .person { position: absolute; right: 40px; top: 92px; text-align: left; color: var(--ink); }
  .person-name { font-family: var(--name-font); font-weight: 700; font-size: 27px; letter-spacing: 0.5px; line-height: 1; }
  .person-role { font-size: 12.5px; margin-top: 3px; }

  .contacts {
    position: absolute;
    right: 22px;
    bottom: 20px;
    list-style: none;
    color: var(--white);
    font-size: 13.5px;
  }
  .contacts li {
    display: flex;
    justify-content: flex-end;
    align-items: center;
    gap: 12px;
    height: 24px;
  }
  .contacts svg { width: 16px; height: 16px; flex: none; }
</style>
</head>
<body>

  <section class="card card-back" aria-label="Card back">
    <svg class="card-waves" viewBox="0 0 600 343" preserveAspectRatio="none" aria-hidden="true">
      <path fill="var(--sage)" d="M0 258 C 140 215, 300 205, 420 210 C 500 214, 560 222, 600 232 L600 240 C 560 230, 500 222, 420 220 C 300 217, 140 228, 0 272 Z"/>
      <path fill="var(--peach-light)" d="M0 285 C 140 235, 300 222, 420 226 C 500 229, 560 236, 600 246 L600 343 L0 343 Z"/>
    </svg>
    <div class="brand">
      <span class="brand-dot"></span>
      <span>Tidewell:<br>Oedema &amp; Family Clinic</span>
    </div>
  </section>

  <section class="card card-front" aria-label="Card front">
    <svg class="card-waves" viewBox="0 0 600 343" preserveAspectRatio="none" aria-hidden="true">
      <path fill="var(--sage)" d="M0 262 C 130 300, 280 262, 390 208 C 470 172, 560 180, 600 222 L600 236 C 560 196, 480 188, 410 212 C 290 254, 140 312, 0 288 Z"/>
      <path fill="var(--peach)" d="M0 306 C 150 322, 300 262, 420 218 C 500 190, 565 200, 600 240 L600 343 L0 343 Z"/>
    </svg>

    <div class="brand">
      <span class="brand-dot"></span>
      <span>Tidewell:<br>Oedema &amp; Family Clinic</span>
    </div>

    <div class="person">
      <p class="person-name">MARA ELLISON</p>
      <p class="person-role">CEO/Managing Director</p>
    </div>

    <ul class="contacts">
      <li>8431 6570
        <svg viewBox="0 0 16 16" aria-label="Phone"><path fill="var(--white)" d="M3.2 1.5l2.2 2.6-1.3 1.6c.8 1.9 2.3 3.4 4.2 4.2l1.6-1.3 2.6 2.2-1.4 2.4C6.3 13 3 9.7 2.8 2.9z"/></svg>
      </li>
      <li>8431 6578
        <svg viewBox="0 0 16 16" aria-label="Mobile"><rect x="4.5" y="1" width="7" height="14" rx="1.2" fill="none" stroke="var(--white)" stroke-width="1.4"/><circle cx="8" cy="12.6" r="0.8" fill="var(--white)"/></svg>
      </li>
      <li>info@tidewellcareservices.com.au
        <svg viewBox="0 0 16 16" aria-label="Email"><rect x="1.5" y="3.5" width="13" height="9" fill="none" stroke="var(--white)" stroke-width="1.3"/><path d="M1.5 3.5 8 9l6.5-5.5" fill="none" stroke="var(--white)" stroke-width="1.3"/></svg>
      </li>
      <li>tidewellcareservices.com.au
        <svg viewBox="0 0 16 16" aria-label="Website"><g fill="none" stroke="var(--white)" stroke-width="1.2"><circle cx="8" cy="8" r="6.5"/><ellipse cx="8" cy="8" rx="3" ry="6.5"/><path d="M1.5 8h13M2.6 4.6h10.8M2.6 11.4h10.8"/></g></svg>
      </li>
    </ul>
  </section>

</body>
</html>
```